folding sales brochure

We need a brochure in the colors of orange, black and charcoal gray - our logo colors.
www.vennotraduxpartners

Strong, clean - and something eye catching.

We are looking for graphic images and photos that depict international business, written translation, live simultaneous interpretation for conferences & events with people communicating. We have some photos, but are open to others.

This brochure will generalize our companies services.
This brochure will be used for B2B as well as Trade Show booths.
Updates

Reason: Project has been extended to allow time for feedback and completion. Thank you all... some wonderful designs.

Thank you all for your designs - they were all creative in so many different ways, making the choice of just one very difficult.

regards,
Delia

Target Market(s)

Our target is large global corporate companies.

Industry/Entity Type

Events

Requirements
Must have
• company logo (will supply)
company website and address etc.

Our Type Font is: Helvetica Neue LT Std

All info needed can be found here: www.vennotraduxpartners
Should not have
• we feel globes and flags are overdone in the International marketplace - hopefully you can find something else to speak Global.

```html
<!DOCTYPE html>
<html lang="en">
<head>
<meta charset="utf-8">
<title>Vennotradux Partners – Folding Sales Brochure, Inside Spread</title>
<link rel="stylesheet" href="https://fonts.googleapis.com/css2?family=Arimo:wght@400;700&display=swap">
<style>
  :root {
    --orange: #f0832a;
    --orange-strip: #f6a84a;
    --charcoal: #4b4b4d;
    --gray-mid: #8c8c8e;
    --paper: #ffffff;
    --text: #3c3c3c;
    --label: #b5b5b5;
    --frame: #9a9a9a;
    --dot-dark: #8c8c8e;
    --dot-mid: #b0b0b2;
    --dot-light: #c8c8ca;
  }
  * { margin: 0; padding: 0; box-sizing: border-box; }
  html, body { width: 1200px; height: 898px; overflow: hidden; background: var(--paper); }
  body { font-family: "Arimo", "Helvetica Neue", Helvetica, Arial, sans-serif; color: var(--text); }

  .canvas { position: relative; width: 1200px; height: 898px; border: 1px solid var(--frame); }

  .page-label { position: absolute; top: 6px; font-size: 22px; color: var(--label); font-weight: 400; }
  .page-label--left { left: 258px; }
  .page-label--right { left: 829px; }

  .panel { position: absolute; top: 36px; width: 583px; height: 823px; overflow: hidden; }
  .panel--left { left: 17px; }
  .panel--right { left: 600px; width: 582px; }

  .panel__upper {
    position: absolute; left: 0; top: 0; width: 100%; height: 515px;
    background: linear-gradient(180deg, #e9e9ea 0%, #f7f7f7 35%, #ffffff 60%, #eeeeef 100%);
  }
  .panel--right .panel__upper { background: linear-gradient(200deg, #dcdcdd 0%, #f3f3f3 40%, #ffffff 65%, #ededee 100%); }

  .section-title { position: absolute; font-size: 15px; font-weight: 700; color: var(--orange); white-space: nowrap; display: flex; align-items: center; gap: 4px; }
  .body-copy { position: absolute; font-size: 10.4px; line-height: 15px; text-align: justify; color: var(--text); }

  .dots { display: inline-block; vertical-align: middle; }

  .photo { position: absolute; }
  .photo--monitors { background: linear-gradient(135deg, #1a1a1f 0%, #3a4a6a 45%, #6a7fa0 55%, #151518 100%); }
  .photo--booth { background: linear-gradient(160deg, #6a4a32 0%, #c9a57c 50%, #8a6a4a 100%); }
  .photo--ballroom { background: linear-gradient(120deg, #3a1f33 0%, #8a4c7a 35%, #b38aa8 60%, #4a2a3a 100%); }
  .photo--microphone { background: linear-gradient(135deg, #222 0%, #5a5a5a 50%, #2a2a2a 100%); }
  .photo--meeting { background: linear-gradient(150deg, #4a2d1a 0%, #8e6a48 45%, #d9c9b0 75%, #5a3d28 100%); }

  .feature-title { position: absolute; font-size: 22px; line-height: 28px; color: var(--orange); text-transform: uppercase; font-weight: 400; }

  .orange-block { position: absolute; top: 515px; height: 213px; background: var(--orange); }
  .orange-block__text { position: absolute; font-size: 18px; line-height: 23px; color: var(--paper); text-transform: uppercase; }

  .footer-band { position: absolute; left: 0; top: 728px; width: 100%; height: 84px; background: linear-gradient(180deg, #9a9a9c 0%, #7a7a7c 45%, var(--charcoal) 100%); }
  .footer-band__url { position: absolute; top: 68px; font-size: 9px; color: var(--paper); letter-spacing: 0.2px; }
  .footer-strip { position: absolute; left: 0; top: 812px; width: 100%; height: 11px; background: var(--orange-strip); }
</style>
</head>
<body>
<div class="canvas">
  <div class="page-label page-label--left">Inside left</div>
  <div class="page-label page-label--right">Inside Right</div>

  <section class="panel panel--left">
    <div class="panel__upper"></div>

    <h2 class="section-title" style="left:35px; top:52px;">Language solutions for today
      <svg class="dots" width="40" height="16" viewBox="0 0 40 16"><circle cx="6" cy="8" r="5" fill="var(--dot-dark)"/><circle cx="20" cy="8" r="6" fill="var(--dot-mid)"/><circle cx="33" cy="8" r="3" fill="var(--dot-light)"/></svg>
    </h2>
    <p class="body-copy" style="left:35px; top:82px; width:250px;">“Language Solutions” are the services that allow communication to transcend language barriers. We begin with translators and interpreters and finish with the technology to bring it all together. Our solutions are just that: answers to problems. We meet your needs so you don’t have to worry. Through Vennotradux, you communicate with your global audience with equal respect. We are a nationwide leader in live event language services, which includes simultaneous interpreters, interpreting equipment, and push-to-talk discussion systems. Our translation division has decades of experience and millions of words under its belt. Today, these services include a full range of studio services like voiceover and subtitles.</p>
    <div class="photo photo--monitors" role="img" aria-label="Control room with a wall of broadcast monitors" style="left:312px; top:84px; width:232px; height:184px;"></div>

    <h2 class="section-title" style="right:31px; top:332px;">
      <svg class="dots" width="40" height="16" viewBox="0 0 40 16"><circle cx="6" cy="8" r="3" fill="var(--dot-light)"/><circle cx="19" cy="8" r="6" fill="var(--dot-mid)"/><circle cx="33" cy="8" r="5" fill="var(--dot-dark)"/></svg>
      Language solutions for today
    </h2>
    <div class="photo photo--booth" role="img" aria-label="Conference table with interpreting headsets and receivers" style="left:35px; top:360px; width:212px; height:138px;"></div>
    <p class="body-copy" style="left:289px; top:360px; width:263px;">“Language Solutions” are the services that allow communication to transcend language barriers. We begin with translators and interpreters and finish with the technology to bring it all together. Our solutions are just that: answers to problems. We meet your needs so you don’t have to worry. Through Vennotradux, you communicate with your global audience with equal respect.</p>

    <div class="orange-block" style="left:0; width:213px;">
      <p class="orange-block__text" style="left:25px; top:62px;">Live event<br>interpretation,<br>unlimited<br>languages
        <svg class="dots" width="40" height="14" viewBox="0 0 40 14"><circle cx="6" cy="7" r="5" fill="#fff"/><circle cx="19" cy="7" r="6" fill="#fde3cc"/><circle cx="32" cy="7" r="3.5" fill="#fff"/></svg>
      </p>
    </div>
    <div class="photo photo--ballroom" role="img" aria-label="Ballroom with a row of interpreting booths" style="left:213px; top:515px; width:370px; height:213px;"></div>

    <div class="footer-band" role="img" aria-label="Charcoal footer band with abstract light graphic">
      <span class="footer-band__url" style="left:223px;">www.vennotraduxpartners.com</span>
    </div>
    <div class="footer-strip"></div>
  </section>

  <section class="panel panel--right">
    <div class="panel__upper"></div>

    <div class="photo photo--microphone" role="img" aria-label="Studio microphone with pop filter and headphones" style="left:42px; top:84px; width:230px; height:150px;"></div>
    <h2 class="feature-title" style="left:299px; top:104px;">In house<br>voice-over<br>and subtitling<br>services
      <svg class="dots" width="40" height="16" viewBox="0 0 40 16"><circle cx="6" cy="8" r="5" fill="var(--dot-dark)"/><circle cx="20" cy="8" r="6" fill="var(--dot-mid)"/><circle cx="33" cy="8" r="3" fill="var(--dot-light)"/></svg>
    </h2>
    <p class="body-copy" style="left:37px; top:272px; width:522px;">“Language Solutions” are the services that allow communication to transcend language barriers. We begin with translators and interpreters and finish with the technology to bring it all together. Our solutions are just that: answers to problems. We meet your needs so you don’t have to worry. Through Vennotradux, you communicate with your global audience with equal respect. We are a nationwide leader in live event language services, which includes simultaneous interpreters, interpreting equipment, and push-to-talk discussion systems. Our translation division has decades of experience and millions of words under its belt. Today, these services include a full range of studio services like voiceover and subtitles.</p>

    <div class="orange-block" style="left:0; width:215px;">
      <p class="orange-block__text" style="left:23px; top:51px;">Meetings:<br>let everyone<br>speak,<br>and be<br>understood
        <svg class="dots" width="40" height="14" viewBox="0 0 40 14"><circle cx="6" cy="7" r="5" fill="#fff"/><circle cx="19" cy="7" r="6" fill="#fde3cc"/><circle cx="32" cy="7" r="3.5" fill="#fff"/></svg>
      </p>
    </div>
    <div class="photo photo--meeting" role="img" aria-label="Long meeting table set with microphones and chairs" style="left:215px; top:515px; width:367px; height:213px;"></div>

    <div class="footer-band" role="img" aria-label="Charcoal footer band with abstract light graphic">
      <span class="footer-band__url" style="left:223px;">www.vennotraduxpartners.com</span>
    </div>
    <div class="footer-strip"></div>
  </section>
</div>
</body>
</html>
```